IT Company that provides secure IT solutions and services to our customers

We need business cards and a logo for a new IT Solutions company just created based in Kuala Lumpur, Malaysia. But will also be serving other countries in the region. We provide secure data, voice solutions on mobile platforms. Our first offering is encrypted voice and data solutions for IOS, Android, Windows and BlackBerry devices.

Target Market(s)

large organizations Govt, Police, Defence, Anti-corruption, Legal, highly regulated industries such as Health-care, Financial, Banking, Insurance,

Industry/Entity Type

Information Technology

Contact Information for Business Card

VelmoraNet (Logo - colour is ORVEX blue)Roshan Adeel Managing Director Kryption IT Sdn. Bhd.5th Floor, Block D, Wisma PLB,No.14 Jalan Seri Melor,50470, Kuala LumpurMalaysia

Font styles to use
Sans Serif

Colors
3176b5
ec1f27
fbed22

Requirements
Must have
• VelmoraNet all in Blue like ORVEX blue. A logo design perhaps a play of VN, K with a dangling T (colour can be any)
Nice to have
• I want a clean crisp card, not too busy, easy to read.

```html
<!DOCTYPE html>
<html lang="en">
<head>
<meta charset="utf-8">
<title>VelmoraNet Business Card</title>
<link rel="stylesheet" href="https://fonts.googleapis.com/css2?family=Source+Sans+3:wght@400;600;800&display=swap">
<style>
  :root {
    --backdrop-top: #2a2a2a;
    --backdrop-bottom: #050505;
    --card-white: #ffffff;
    --brand-red: #c8282c;
    --back-red: #cc2b2e;
    --ink: #1c1c1c;
    --text-font: "Source Sans 3", "Helvetica Neue", Arial, sans-serif;
  }
  html, body {
    margin: 0;
    padding: 0;
    width: 1200px;
    height: 900px;
    overflow: hidden;
  }
  .stage {
    position: relative;
    width: 1200px;
    height: 900px;
    background: linear-gradient(180deg, var(--backdrop-top) 0%, #161616 55%, var(--backdrop-bottom) 100%);
    font-family: var(--text-font);
  }
  .card {
    position: absolute;
    top: 306px;
    width: 439px;
    height: 271px;
    border-radius: 12px;
    box-shadow: 0 2px 6px rgba(0,0,0,0.35);
  }
  .card-front { left: 149px; background: var(--card-white); }
  .card-back { left: 609px; background: var(--back-red); }

  .brand {
    position: absolute;
    display: flex;
    align-items: center;
  }
  .brand-circle { display: block; flex: none; }
  .brand-name {
    font-family: var(--text-font);
    font-weight: 800;
    letter-spacing: -0.5px;
    line-height: 1;
  }
  .card-front .brand { left: 62px; top: 44px; }
  .card-front .brand-circle { margin-right: 22px; }
  .card-front .brand-name { font-size: 46px; color: var(--ink); }

  .card-back .brand { left: 182px; top: 198px; }
  .card-back .brand-circle { margin-right: 14px; }
  .card-back .brand-name { font-size: 31px; color: var(--card-white); }

  .contact {
    position: absolute;
    left: 139px;
    top: 110px;
    color: var(--ink);
    font-size: 13px;
    line-height: 16px;
  }
  .person-name {
    margin: 0;
    font-size: 15.5px;
    font-weight: 600;
    color: var(--brand-red);
    line-height: 18px;
  }
  .person-role { margin: 0 0 20px; }
  .company-name {
    margin: 0;
    font-size: 14.5px;
    font-weight: 600;
    color: var(--brand-red);
    line-height: 18px;
  }
  .address { margin: 0; font-style: normal; }
</style>
</head>
<body>
<main class="stage">
  <section class="card card-front" aria-label="Business card front">
    <div class="brand">
      <svg class="brand-circle" width="54" height="54" viewBox="0 0 54 54" aria-hidden="true">
        <circle cx="27" cy="27" r="24.5" fill="none" stroke="var(--brand-red)" stroke-width="3"/>
      </svg>
      <span class="brand-name">VelmoraNet</span>
    </div>
    <div class="contact">
      <p class="person-name">Roshan Adeel</p>
      <p class="person-role">Managing Director</p>
      <p class="company-name">Velmora Net</p>
      <address class="address">
        Sdn. Bhd.5th Floor, Block D,<br>
        Wisma PLB,No.14 Jalan Seri Melor,<br>
        50470, Kuala Lumpur<br>
        Malaysia
      </address>
    </div>
  </section>

  <section class="card card-back" aria-label="Business card back">
    <div class="brand">
      <svg class="brand-circle" width="38" height="38" viewBox="0 0 38 38" aria-hidden="true">
        <circle cx="19" cy="19" r="17" fill="none" stroke="var(--card-white)" stroke-width="2.5"/>
      </svg>
      <span class="brand-name">VelmoraNet</span>
    </div>
  </section>
</main>
</body>
</html>
```